wealth management firm, professional group, new model

we have a logo that works but we need a card, white background using our colors...clean look

our tag line if can be used in

Your Path From Client to Partner

```html
<!DOCTYPE html>
<html lang="en">
<head>
<meta charset="utf-8">
<title>Arvell Wealth Partners – Business Card</title>
<link href="https://fonts.googleapis.com/css2?family=Montserrat:wght@400;500;700;800&display=swap" rel="stylesheet">
<style>
  :root {
    --navy: #1b2d52;
    --grey: #9b9b9b;
    --white: #ffffff;
    --ink: #1a1a1a;
    --stage: #2e2e2e;
  }
  * { margin: 0; padding: 0; box-sizing: border-box; }
  html, body { width: 1200px; height: 689px; overflow: hidden; }
  body {
    background: var(--stage);
    font-family: "Montserrat", Arial, sans-serif;
    position: relative;
  }
  .card {
    position: absolute;
    top: 190px;
    width: 540px;
    height: 309px;
    border-radius: 18px;
    overflow: hidden;
  }
  .card--front { left: 40px; background: var(--navy); }
  .card--back { left: 620px; background: var(--white); }

  .wordmark {
    position: absolute;
    text-align: center;
    font-weight: 500;
    text-transform: uppercase;
    line-height: 1.5;
  }
  .card--front .wordmark {
    left: 0; right: 0; top: 112px;
    color: var(--white);
    font-size: 26px;
    letter-spacing: 0.34em;
  }
  .card--back .wordmark {
    left: 20px; width: 250px; top: 92px;
    color: var(--navy);
    font-size: 17px;
    letter-spacing: 0.26em;
  }

  .divider {
    position: absolute;
    left: 292px; top: 46px;
    width: 1.5px; height: 128px;
    background: var(--navy);
  }
  .details {
    position: absolute;
    left: 306px; top: 40px;
    color: var(--ink);
  }
  .details__name {
    color: var(--navy);
    font-weight: 800;
    font-size: 19px;
    letter-spacing: 0.01em;
    line-height: 1.1;
  }
  .details__title { font-size: 11.5px; font-weight: 500; margin-top: 3px; }
  .details__tagline { font-size: 11.5px; font-weight: 500; margin-top: 9px; }
  .contact { list-style: none; margin-top: 7px; }
  .contact li {
    display: flex; align-items: center; gap: 7px;
    font-size: 11.5px; font-weight: 500; line-height: 19px;
  }
  .contact svg { width: 12px; height: 12px; flex: none; }

  .footer-rule {
    position: absolute;
    left: 0; right: 0; bottom: 52px;
    height: 6px;
    background: var(--grey);
  }
  .footer-band {
    position: absolute;
    left: 0; right: 0; bottom: 0;
    height: 46px;
    background: var(--navy);
  }
</style>
</head>
<body>

  <section class="card card--front" aria-label="Card front">
    <div class="wordmark">Arvell<br>Wealth Partners</div>
  </section>

  <section class="card card--back" aria-label="Card back">
    <div class="footer-rule"></div>
    <div class="footer-band"></div>

    <div class="wordmark">Arvell<br>Wealth Partners</div>
    <div class="divider"></div>

    <div class="details">
      <p class="details__name">DANIEL WHITCOMBE</p>
      <p class="details__title">Managing Director</p>
      <p class="details__tagline">Your Path From Client to Partner</p>
      <ul class="contact">
        <li>
          <svg viewBox="0 0 12 12"><rect x="3" y="0.75" width="6" height="10.5" rx="1.2" fill="none" stroke="var(--navy)" stroke-width="1.2"/><line x1="5" y1="9.5" x2="7" y2="9.5" stroke="var(--navy)" stroke-width="1"/></svg>
          555-014-2298
        </li>
        <li>
          <svg viewBox="0 0 12 12"><rect x="0.5" y="2" width="11" height="8" fill="var(--navy)"/><path d="M0.5,2 L6,6.5 L11.5,2" fill="none" stroke="var(--white)" stroke-width="1"/></svg>
          hello@arvellwealth.com
        </li>
        <li>
          <svg viewBox="0 0 12 12"><circle cx="6" cy="6" r="5.5" fill="var(--navy)"/><path d="M0.5,6 H11.5 M6,0.5 C3.5,3 3.5,9 6,11.5 M6,0.5 C8.5,3 8.5,9 6,11.5" fill="none" stroke="var(--white)" stroke-width="0.8"/></svg>
          www.arvellwealthpartners.com
        </li>
      </ul>
    </div>
  </section>

</body>
</html>
```